Bright Harbor Counseling Letterhead for hip modern business

I would like some ombre use of the colors in the logo hip letterhead that incorporates logo colors and feel, needs to connect with young professionals and college students. i need to be able to write letters to schools to excuse absences as well. i like color blocks on one side preferably using colors from the attached logo design.

Target Market(s)

high income young people, young adults and college students

Industry/Entity Type

mental health

Font styles to use
Serif
Sans Serif

Colors
0054AA
0677BA
7BADD7
CADEEF
E8F1F8
0094D4
00A9DD
6FCCEA
C7EBF8
E9F6FB
00AB8E
00BBA5
67D7C9
C6EFE9
E9F9F6
59FF00
82FF00
B8FF75
E3FFCB
F4FFEA
A7469A
B969AE
D3A5CF
EDDBEB
F8F0F9
6B429C
8869AF
B7A5CE
E3DAEB
F3F0F8

Requirements
Must have
• a modern hip feel, somewhat color

```html
<!DOCTYPE html>
<html lang="en">
<head>
<meta charset="utf-8">
<title>Bright Harbor Counseling Letterhead</title>
<link rel="stylesheet" href="https://fonts.googleapis.com/css2?family=Lato:wght@300&family=Open+Sans:wght@400;700&display=swap">
<style>
  :root {
    --backdrop: #dfe2e3;
    --paper: #ffffff;
    --plum: #a7469a;
    --plum-mid: #b969ae;
    --plum-soft: #d3a5cf;
    --plum-pale: #eddbeb;
    --ink: #4a4a4a;
    --ink-muted: #6d6d6d;
    --rule: #d6d6d6;
  }
  * { box-sizing: border-box; margin: 0; padding: 0; }
  html, body {
    width: 1200px; height: 784px; overflow: hidden;
    background: var(--backdrop);
  }
  .canvas {
    position: relative; width: 1200px; height: 784px;
    display: flex; align-items: center; justify-content: center;
  }
  .letterhead {
    position: relative; width: 572px; height: 740px;
    background: var(--paper);
    box-shadow: 0 6px 18px rgba(0,0,0,0.12);
    overflow: hidden;
  }
  .side-band {
    position: absolute; left: 0; top: 0; width: 34px; height: 740px;
    background: linear-gradient(to bottom, var(--plum) 0%, var(--plum-mid) 35%, var(--plum-soft) 75%, var(--plum-pale) 100%);
  }
  .brand {
    position: absolute; left: 66px; top: 22px;
    display: flex; align-items: center; gap: 12px;
  }
  .brand-name {
    font-family: "Lato", sans-serif; font-weight: 300;
    color: var(--ink); line-height: 1.05;
  }
  .brand-name .line-main { display: block; font-size: 30px; }
  .brand-name .line-sub { display: block; font-size: 15px; letter-spacing: 4px; text-align: right; margin-top: 2px; }
  .brand-dot {
    width: 22px; height: 22px; border-radius: 50%;
    background: var(--plum-mid); flex: none;
  }
  .contact-rule {
    position: absolute; right: 246px; top: 106px; width: 110px; height: 1px;
    background: var(--rule);
  }
  .contact {
    position: absolute; right: 22px; top: 100px; width: 214px;
    list-style: none;
    font-family: "Open Sans", sans-serif; font-size: 10.5px; line-height: 1.35;
    color: var(--ink-muted);
  }
  .contact li { display: flex; align-items: flex-start; gap: 6px; margin-bottom: 3px; }
  .contact .address { color: var(--plum); font-weight: 700; }
  .contact .icon { width: 11px; height: 11px; flex: none; margin-top: 2px; }
</style>
</head>
<body>
<main class="canvas">
  <article class="letterhead">
    <div class="side-band" aria-hidden="true"></div>

    <header class="brand">
      <div class="brand-name">
        <span class="line-main">Bright Harbor</span>
        <span class="line-sub">Counseling</span>
      </div>
      <span class="brand-dot"></span>
    </header>

    <div class="contact-rule"></div>

    <ul class="contact">
      <li class="address">
        <svg class="icon" viewBox="0 0 12 12"><circle cx="6" cy="6" r="6" fill="var(--plum)"/><path d="M6 2.6a2 2 0 0 0-2 2c0 1.6 2 4.2 2 4.2s2-2.6 2-4.2a2 2 0 0 0-2-2z" fill="#fff"/></svg>
        <span>0000 Sample Lane, Ste 140,<br>California, 90000, United States</span>
      </li>
      <li>
        <svg class="icon" viewBox="0 0 12 12"><circle cx="6" cy="6" r="6" fill="var(--plum)"/><path d="M4 3.2l1.1 1.3-.6.8c.4.8 1 1.4 1.8 1.8l.8-.6 1.3 1.1-.7 1C5.9 8.5 3.5 6.1 3.4 4z" fill="#fff"/></svg>
        <span>(555) 010-2040</span>
      </li>
      <li>
        <svg class="icon" viewBox="0 0 12 12"><circle cx="6" cy="6" r="6" fill="var(--plum)"/><rect x="3.3" y="4.2" width="5.4" height="3.8" fill="#fff"/><rect x="4.2" y="2.8" width="3.6" height="1.6" fill="#fff"/></svg>
        <span>(555) 010-2041</span>
      </li>
      <li>
        <svg class="icon" viewBox="0 0 12 12"><circle cx="6" cy="6" r="6" fill="var(--plum)"/><rect x="3" y="3.8" width="6" height="4.4" fill="#fff"/><path d="M3 3.8l3 2.4 3-2.4" fill="none" stroke="var(--plum)" stroke-width="0.7"/></svg>
        <span>hello@brightharbor.com</span>
      </li>
      <li>
        <svg class="icon" viewBox="0 0 12 12"><circle cx="6" cy="6" r="6" fill="var(--plum)"/><circle cx="6" cy="6" r="3" fill="none" stroke="#fff" stroke-width="0.8"/><path d="M3 6h6M6 3c1.4 1.6 1.4 4.4 0 6M6 3c-1.4 1.6-1.4 4.4 0 6" fill="none" stroke="#fff" stroke-width="0.6"/></svg>
        <span>www.brightharbor.com</span>
      </li>
    </ul>
  </article>
</main>
</body>
</html>
```